Duct Manufacturing Company new to the industry needs business card and stationary design

we are sheet metal duct manufacturers looking for a business card design to fit my new business logo.
nothing to crazy that will date, but want it to stand out from the crowed.
I'm sure you guys will work it out.

Contact Information for Business Card

Glen Marsh
Director

Address
17 Dorwell St
Larkfield NSW 2714

0438 760 514

Sales@flowbend.com.au

Font styles to use
Other font styles liked:
• BankGothic md bt

Requirements
Nice to have
• Like the idea of corner rounded to match logo
• like to keep colours flowing
• font I like sharp square not rounded

```html
<!DOCTYPE html>
<html lang="en">
<head>
<meta charset="UTF-8">
<title>Flowbend Industries – Business Card</title>
<link href="https://fonts.googleapis.com/css2?family=Michroma&family=Montserrat:wght@400;500&display=swap" rel="stylesheet">
<style>
  :root {
    --backdrop: #a4a4a4;
    --card: #ffffff;
    --green: #5fb833;
    --green-deep: #2f9e3f;
    --blue: #1b63ad;
    --grey-text: #4a4a4a;
    --grey-soft: #6b6b6b;
  }
  html, body {
    margin: 0;
    width: 1200px;
    height: 1200px;
    overflow: hidden;
    background: var(--backdrop);
    font-family: "Montserrat", Arial, sans-serif;
  }
  .card {
    position: absolute;
    width: 712px;
    height: 418px;
    background: var(--card);
    border-radius: 28px;
    overflow: hidden;
  }
  .card--front { left: 238px; top: 118px; }
  .card--back  { left: 230px; top: 644px; }
  .card__band {
    position: absolute;
    left: 0; bottom: 0;
    width: 712px; height: 18px;
  }
  .brand-name {
    font-family: "Michroma", "Arial Black", sans-serif;
    color: var(--green-deep);
    line-height: 1.15;
    letter-spacing: 1px;
    margin: 0;
  }
  .card--front .brand {
    position: absolute;
    left: 0; right: 0; top: 248px;
    text-align: center;
  }
  .card--front .brand-name { font-size: 34px; }
  .card--front .brand-name span { display: block; font-size: 26px; letter-spacing: 6px; }
  .card--back .brand {
    position: absolute;
    left: 224px; top: 80px;
    display: flex; align-items: center; gap: 16px;
  }
  .brand-mark {
    width: 22px; height: 22px; border-radius: 50%;
    background: var(--green-deep);
  }
  .card--back .brand-name { font-size: 33px; }
  .card--back .brand-name span { display: block; font-size: 26px; letter-spacing: 6px; }
  .contact {
    position: absolute;
    left: 262px; top: 184px;
    color: var(--grey-text);
  }
  .contact__name {
    font-family: "Michroma", "Arial Black", sans-serif;
    color: var(--blue);
    font-size: 21px;
    letter-spacing: 1px;
    margin: 0;
  }
  .contact__role { font-size: 17px; color: var(--grey-soft); margin: 4px 0 22px; }
  .contact__list { list-style: none; margin: 0; padding: 0; font-size: 19px; }
  .contact__list li { display: flex; align-items: center; height: 27px; }
  .contact__list svg { width: 18px; height: 16px; margin-right: 17px; fill: var(--blue); }
  .contact__address { font-size: 19px; margin: 3px 0 0; }
</style>
</head>
<body>

<section class="card card--front">
  <div class="brand">
    <p class="brand-name">FLOWBEND<span>INDUSTRIES</span></p>
  </div>
  <svg class="card__band" viewBox="0 0 712 18" preserveAspectRatio="none">
    <defs>
      <linearGradient id="frontGreen" x1="0" x2="1">
        <stop offset="0" stop-color="#1f9a44"/><stop offset="1" stop-color="#8cc63f"/>
      </linearGradient>
      <linearGradient id="frontBlue" x1="0" x2="1">
        <stop offset="0" stop-color="#1e9ae0"/><stop offset="1" stop-color="#1b5ea8"/>
      </linearGradient>
    </defs>
    <polygon points="0,0 500,0 470,18 0,18" fill="url(#frontGreen)"/>
    <polygon points="506,0 712,0 712,18 476,18" fill="url(#frontBlue)"/>
  </svg>
</section>

<section class="card card--back">
  <div class="brand">
    <div class="brand-mark"></div>
    <p class="brand-name">FLOWBEND<span>INDUSTRIES</span></p>
  </div>
  <div class="contact">
    <p class="contact__name">GLEN MARSH</p>
    <p class="contact__role">Director</p>
    <ul class="contact__list">
      <li><svg viewBox="0 0 18 16"><path d="M1 5c0-2 4-4 8-4s8 2 8 4v1h-4V4.5H5V6H1z"/><rect x="3" y="7" width="12" height="8" rx="1.5"/></svg>0438 760 514</li>
      <li><svg viewBox="0 0 16 16"><circle cx="8" cy="8" r="7" fill="none" stroke="#1b63ad" stroke-width="1.6"/><ellipse cx="8" cy="8" rx="3" ry="7" fill="none" stroke="#1b63ad" stroke-width="1.4"/><path d="M1 8h14" stroke="#1b63ad" stroke-width="1.4"/></svg>flowbend.com.au</li>
      <li><svg viewBox="0 0 18 14"><rect x="0.5" y="1" width="17" height="12" fill="none" stroke="#1b63ad" stroke-width="1.6"/><path d="M1 1l8 7 8-7M1 13l6-6M17 13l-6-6" fill="none" stroke="#1b63ad" stroke-width="1.4"/></svg>Sales@flowbend.com.au</li>
    </ul>
    <p class="contact__address">17 Dorwell St Larkfield NSW 2714</p>
  </div>
  <svg class="card__band" viewBox="0 0 712 18" preserveAspectRatio="none">
    <polygon points="0,0 500,0 470,18 0,18" fill="#6cbf3a"/>
    <polygon points="506,0 712,0 712,18 476,18" fill="#1b5ea8"/>
  </svg>
</section>

</body>
</html>
```